Album Cover Art for New Single

Independent singer-songwriter and pianist, seeking design work for a new single "Walk Beside the Lantern". Christian & Gospel music format. See attached for master recording.

This single is personal for me, so I'm looking for an image that really captures the heart of the message. Redemption, forgiveness, prodigals returning home to a loving father.
Updates

Target Market(s)

Millenials

Colors

Designer to choose colors to be used in the design.

Requirements
Must have
• simple graphic, must include the following text:
• Walk Beside the Lantern
• Dale Verrick
Should not have
• Avoid "cheesy" look and feel.

```html
<!DOCTYPE html>
<html lang="en">
<head>
<meta charset="utf-8">
<title>Walk Beside the Lantern — Dale Verrick</title>
<link rel="stylesheet" href="https://fonts.googleapis.com/css2?family=Montserrat:wght@200;700&family=Cinzel:wght@500&display=swap">
<style>
  :root {
    --sky: #c4cbcd;
    --haze: #8e999b;
    --water: #5d6d70;
    --deep: #2f3b3e;
    --ink: #ffffff;
  }
  html, body {
    margin: 0;
    padding: 0;
    width: 1200px;
    height: 1200px;
    overflow: hidden;
    background: var(--deep);
  }
  .cover {
    position: relative;
    width: 1200px;
    height: 1200px;
    overflow: hidden;
  }
  .cover-photo {
    position: absolute;
    inset: 0;
    background:
      radial-gradient(ellipse 55% 30% at 42% 30%, rgba(110, 40, 60, 0.55), rgba(110, 40, 60, 0) 70%),
      linear-gradient(180deg, var(--sky) 0%, var(--haze) 40%, var(--water) 62%, var(--deep) 100%);
  }
  .title-art {
    position: absolute;
    inset: 0;
    width: 1200px;
    height: 1200px;
  }
  .title-word {
    fill: var(--ink);
    font-family: "Montserrat", sans-serif;
  }
  .title-word--bold {
    font-weight: 700;
    font-size: 130px;
    letter-spacing: 2px;
  }
  .title-word--thin {
    font-weight: 200;
  }
  .title-word--left { font-size: 112px; letter-spacing: 4px; }
  .title-word--mid { font-size: 150px; letter-spacing: 4px; }
  .title-word--low { font-size: 100px; letter-spacing: 3px; }
  .artist-name {
    position: absolute;
    left: 0;
    right: 0;
    top: 1082px;
    margin: 0;
    text-align: center;
    color: var(--ink);
    font-family: "Cinzel", serif;
    font-weight: 500;
    font-size: 28px;
    letter-spacing: 22px;
    padding-left: 22px;
  }
</style>
</head>
<body>
  <main class="cover">
    <div class="cover-photo" role="img" aria-label="Photograph of a misty mountain lake with a dark treeline, a silhouetted figure seen from behind raising a flare that trails deep crimson smoke across the sky"></div>
    <svg class="title-art" viewBox="0 0 1200 1200" aria-label="Walk Beside the Lantern">
      <text class="title-word title-word--thin title-word--left" x="60" y="589">BESIDE</text>
      <text class="title-word title-word--bold" x="516" y="516">WALK</text>
      <text class="title-word title-word--thin title-word--mid" x="482" y="657">THE</text>
      <text class="title-word title-word--thin title-word--low" x="648" y="719">LANTERN</text>
    </svg>
    <p class="artist-name">DALE VERRICK</p>
  </main>
</body>
</html>
```